English and Spanish Language School Needs a Business Card

Need a business card design a startup company called Maribel Language School. The company will offer English and Spanish conversational level courses designed to make the learner feel comfortable with grammar and vocabulary. We would like to see a logo with some colour that should communicate learning, growth.

Target Market(s)

Consumers and businesses

Industry/Entity Type

Education

Contact Information for Business Card

TBD

Font styles to use
Serif

Requirements
Must have
• Include the following
• Logo
• Name
• Title
• Cellphone Number
• Office Phone number
• Email address
• Office Address

```html
<!DOCTYPE html>
<html lang="en">
<head>
<meta charset="utf-8">
<title>Maribel Language School – Business Card</title>
<link href="https://fonts.googleapis.com/css2?family=Montserrat:wght@400;500;600;700&display=swap" rel="stylesheet">
<style>
  :root {
    --red: #c81f26;
    --teal: #1aa7ad;
    --white: #ffffff;
    --backdrop: #e9eaec;
    --ink-shadow: rgba(0,0,0,0.18);
  }
  * { box-sizing: border-box; margin: 0; padding: 0; }
  html, body { width: 1200px; height: 900px; overflow: hidden; }
  body {
    background: var(--backdrop);
    font-family: "Montserrat", sans-serif;
    position: relative;
  }
  .card {
    position: absolute;
    width: 700px;
    height: 400px;
    border-radius: 26px;
    overflow: hidden;
    box-shadow: 0 10px 28px var(--ink-shadow);
  }
  .card svg.shapes { position: absolute; inset: 0; }

  /* Front */
  .card--front { left: 70px; top: 40px; background: var(--red); }
  .front-brand {
    position: absolute; left: 190px; top: 110px;
    color: var(--white); font-weight: 700; line-height: 1;
  }
  .front-brand .brand-main { font-size: 76px; letter-spacing: -1px; }
  .front-brand .brand-sub { font-size: 28px; margin-top: 6px; margin-left: 60px; }
  .front-web {
    position: absolute; right: 34px; top: 296px;
    color: var(--white); font-size: 15px; font-weight: 600; letter-spacing: 0.2px;
  }

  /* Back */
  .card--back { left: 430px; top: 470px; background: var(--white); }
  .back-brand {
    position: absolute; left: 46px; top: 96px;
    color: var(--red); font-weight: 700; line-height: 1;
  }
  .back-brand .brand-main { font-size: 66px; letter-spacing: -1px; }
  .back-brand .brand-sub { font-size: 24px; margin-top: 6px; margin-left: 48px; }

  .person {
    position: absolute; right: 70px; top: 40px; text-align: right;
  }
  .person-name { color: var(--red); font-size: 27px; font-weight: 600; letter-spacing: 0.5px; }
  .person-title { color: var(--teal); font-size: 14px; font-weight: 500; margin-top: 2px; }
  .person-rule {
    position: absolute; right: 70px; top: 108px;
    width: 320px; height: 1.5px; background: var(--red);
  }
  .address {
    position: absolute; right: 70px; top: 122px; text-align: right;
    color: var(--teal); font-size: 15px; line-height: 1.35; font-weight: 500;
  }
  .contact-rule {
    position: absolute; left: 150px; top: 250px;
    width: 360px; height: 1.5px; background: var(--red);
  }
  .contacts {
    position: absolute; left: 150px; top: 260px; list-style: none;
    font-size: 16px; line-height: 1.3; color: var(--teal); font-weight: 500;
  }
  .contacts li { display: flex; align-items: center; gap: 12px; }
  .contacts svg { width: 12px; height: 12px; flex: none; }
  .contacts .web { color: var(--red); font-weight: 700; }
</style>
</head>
<body>

<section class="card card--front" aria-label="Business card front">
  <svg class="shapes" viewBox="0 0 700 400" aria-hidden="true">
    <polygon points="0,342 440,342 520,372 700,372 700,400 0,400" fill="var(--white)"/>
    <polygon points="520,352 700,318 700,334 536,366" fill="var(--teal)"/>
  </svg>
  <div class="front-brand">
    <div class="brand-main">Maribel</div>
    <div class="brand-sub">Language School</div>
  </div>
  <div class="front-web">www.maribellanguageschool.com</div>
</section>

<section class="card card--back" aria-label="Business card back">
  <svg class="shapes" viewBox="0 0 700 400" aria-hidden="true">
    <rect x="672" y="34" width="28" height="24" fill="var(--teal)"/>
    <rect x="672" y="58" width="28" height="24" fill="var(--red)"/>
    <polygon points="560,300 700,262 700,400 540,400" fill="var(--red)"/>
    <polygon points="100,386 560,320 556,334 100,400" fill="var(--teal)"/>
  </svg>

  <div class="back-brand">
    <div class="brand-main">Maribel</div>
    <div class="brand-sub">Language School</div>
  </div>

  <div class="person">
    <div class="person-name">Nora Halloway</div>
    <div class="person-title">Director</div>
  </div>
  <div class="person-rule"></div>
  <div class="address">Po Box 218<br>Larkfield VIC 3907</div>

  <div class="contact-rule"></div>
  <ul class="contacts">
    <li>
      <svg viewBox="0 0 12 12"><rect x="3" y="0.5" width="6" height="11" rx="1.2" fill="none" stroke="var(--red)" stroke-width="1.4"/></svg>
      +330 5812-4097
    </li>
    <li>
      <svg viewBox="0 0 12 12"><path d="M2 1 L4.5 1 L5.5 3.5 L4 4.8 Q5.5 7.5 7.2 8 L8.5 6.5 L11 7.5 L11 10 Q6 11.5 2 5 Z" fill="var(--red)"/></svg>
      +330 5817-2268
    </li>
    <li>
      <svg viewBox="0 0 12 12"><rect x="0.7" y="2" width="10.6" height="8" fill="none" stroke="var(--red)" stroke-width="1.4"/><path d="M1 2.5 L6 6.5 L11 2.5" fill="none" stroke="var(--red)" stroke-width="1.2"/></svg>
      hello@maribelschool.com
    </li>
    <li>
      <svg viewBox="0 0 12 12"><circle cx="6" cy="6" r="5.3" fill="var(--red)"/><path d="M0.8 6 H11.2 M6 0.8 Q2.8 6 6 11.2 M6 0.8 Q9.2 6 6 11.2" fill="none" stroke="var(--white)" stroke-width="0.9"/></svg>
      <span class="web">maribellanguageschool.com</span>
    </li>
  </ul>
</section>

</body>
</html>
```